QVR business card

Need a business card for a company that provides instructional design and elearning development services. The website is here: http://quorvane.studio/

I'm attaching a current logo, as well as the old business card design. While I like to keep it clean, the old design is too simplistic for my liking. The only idea I want to reuse from the old design is placing industry jargon on the back of the card, just need a better way to present it. But if you have other ideas for the back--feel free to experiment.

Please use the colors complementary to the color we have on the website. Thank you!

```html
<!DOCTYPE html>
<html lang="en">
<head>
<meta charset="utf-8">
<title>QVR business card</title>
<link href="https://fonts.googleapis.com/css2?family=Open+Sans:wght@400;600;700;800&family=Fira+Sans+Condensed:wght@400;500&display=swap" rel="stylesheet">
<style>
  :root {
    --teal: #22b3b0;
    --teal-deep: #139a98;
    --cream: #e8dc9c;
    --gold: #cdbd7a;
    --ink: #3a3a3a;
    --white: #ffffff;
    --stage: #2c2c30;
  }
  * { box-sizing: border-box; margin: 0; padding: 0; }
  html, body { width: 1200px; height: 925px; overflow: hidden; background: var(--stage); }
  .canvas { position: relative; width: 1200px; height: 925px; }
  .card { position: absolute; width: 580px; height: 331px; overflow: hidden; box-shadow: 0 10px 30px rgba(0,0,0,.45); }

  /* Back of card */
  .card-back { left: 50px; top: 60px; background: var(--teal); color: var(--white); display: flex; align-items: center; padding: 0 34px; }
  .headline { font-family: "Open Sans", sans-serif; font-weight: 800; line-height: .98; letter-spacing: 1px; }
  .headline span { display: block; }
  .headline .l1 { font-size: 50px; }
  .headline .l2 { font-size: 50px; }
  .headline .l3 { font-size: 72px; }
  .headline .l4 { font-size: 50px; }
  .divider { width: 1px; height: 240px; background: rgba(255,255,255,.75); margin: 0 26px; }
  .jargon { list-style: none; font-family: "Fira Sans Condensed", sans-serif; font-weight: 500; font-size: 29px; line-height: 1.35; letter-spacing: .5px; text-transform: uppercase; }

  /* Front of card */
  .card-front { left: 570px; top: 530px; background: var(--white); }
  .gradient-panel { position: absolute; left: 300px; top: 0; right: 0; bottom: 0;
    background: linear-gradient(160deg, var(--cream) 0%, #9fcfb4 45%, var(--teal) 100%);
    border-left: 6px solid var(--teal); }
  .brand { position: absolute; left: 46px; top: 96px; display: flex; align-items: center; gap: 14px; }
  .brand-dot { width: 46px; height: 46px; border-radius: 50%; background: var(--teal); }
  .brand-name { font-family: "Open Sans", sans-serif; font-weight: 700; font-size: 62px; color: var(--gold); letter-spacing: 2px; }
  .name-ribbon { position: absolute; left: 150px; top: 196px; width: 280px; height: 50px; background: var(--teal-deep); color: var(--white);
    font-family: "Open Sans", sans-serif; padding: 6px 0 0 22px; clip-path: polygon(0 0, 100% 0, 93% 50%, 100% 100%, 0 100%, 5% 50%); }
  .name-ribbon .name { font-weight: 700; font-size: 15px; letter-spacing: 1px; text-transform: uppercase; display: block; }
  .name-ribbon .role { font-weight: 400; font-size: 13px; display: block; color: #eafaf9; }
  .contact { position: absolute; left: 340px; top: 40px; font-family: "Open Sans", sans-serif; color: var(--ink); font-size: 14px; line-height: 1.7; }
  .icons { display: flex; gap: 6px; margin-bottom: 6px; }
  .icons svg { width: 20px; height: 20px; }
</style>
</head>
<body>
<main class="canvas">
  <section class="card card-back" aria-label="Card back">
    <h1 class="headline"><span class="l1">HOW</span><span class="l2">CAN</span><span class="l3">WE</span><span class="l4">HELP?</span></h1>
    <div class="divider"></div>
    <ul class="jargon">
      <li>Mobile Learning SCORM</li>
      <li>Instructional Design LMS</li>
      <li>MOOCs eLearning HTML5</li>
      <li>Adult Learning Theory</li>
      <li>Gamification Classroom</li>
      <li>xAPI Blended Learning</li>
    </ul>
  </section>

  <section class="card card-front" aria-label="Card front">
    <div class="gradient-panel"></div>
    <div class="brand">
      <span class="brand-dot"></span>
      <span class="brand-name">QVR</span>
    </div>
    <div class="name-ribbon">
      <span class="name">Marcus Ellwood</span>
      <span class="role">Managing Director</span>
    </div>
    <div class="contact">
      <div class="icons">
        <svg viewBox="0 0 20 20" aria-label="Phone"><circle cx="10" cy="10" r="10" fill="#139a98"/><path d="M7 5h2l1 3-1.5 1a6 6 0 0 0 2.5 2.5L12 10l3 1v2a1 1 0 0 1-1 1A9 9 0 0 1 6 6a1 1 0 0 1 1-1z" fill="#fff"/></svg>
        <svg viewBox="0 0 20 20" aria-label="Email"><circle cx="10" cy="10" r="10" fill="#139a98"/><rect x="5" y="6.5" width="10" height="7" fill="none" stroke="#fff" stroke-width="1.3"/><path d="M5 7l5 4 5-4" fill="none" stroke="#fff" stroke-width="1.3"/></svg>
        <svg viewBox="0 0 20 20" aria-label="Website"><circle cx="10" cy="10" r="10" fill="#139a98"/><circle cx="10" cy="10" r="5" fill="none" stroke="#fff" stroke-width="1.2"/><ellipse cx="10" cy="10" rx="2.2" ry="5" fill="none" stroke="#fff" stroke-width="1.2"/><path d="M5 10h10" stroke="#fff" stroke-width="1.2"/></svg>
      </div>
      <p>555-014-2283</p>
      <p>mellwood@quorvane.studio</p>
      <p>www.quorvane.studio</p>
    </div>
  </section>
</main>
</body>
</html>
```